physical therapy flyer

2 office locations speciality programs - work injury / Motor vehicle accidents - spanish speaking - do not put balance defecits/ fall prevention - Spanish speaking
neck and back pain shoulder pain/ rotator cuff disorder / bursitis
hip pain knee andle and foot pain post operative care including Spine , shoulder , knee , total joint replacement

Meadowlark Physical therapy & Chiropractic
4871 Pinecrest BLvd
dalton heights ny 10592
7185820147
3715 Tillman Parkway
Fernvale NY 10592
7189043218
www.meadowlarkptrehab.com

```html
<!DOCTYPE html>
<html lang="en">
<head>
<meta charset="utf-8">
<title>Meadowlark Physical Therapy &amp; Chiropractic – Flyer</title>
<link rel="stylesheet" href="https://fonts.googleapis.com/css2?family=Poppins:wght@400;500;600;700;800&display=swap">
<style>
  :root{
    --green:#6bb446;
    --green-head:#62ad3f;
    --lavender-top:#eeeef6;
    --lavender-bottom:#d2d2e6;
    --ink:#1d1d24;
    --white:#ffffff;
  }
  *{margin:0;padding:0;box-sizing:border-box;}
  html,body{width:927px;height:1200px;overflow:hidden;background:#e4e4ef;}
  body{font-family:"Poppins",sans-serif;color:var(--ink);}
  .flyer{
    position:relative;width:927px;height:1200px;overflow:hidden;
    background:linear-gradient(180deg,var(--lavender-top) 0%,#e4e4f0 45%,var(--lavender-bottom) 100%);
  }
  .hero-photo{
    position:absolute;left:0;top:0;width:927px;height:480px;
    background:
      linear-gradient(180deg,rgba(238,238,246,0) 70%,#e6e6f1 100%),
      linear-gradient(90deg,#d9d4cf 0%,#ece7e3 35%,#f3f1ef 60%,#eeeef4 100%);
  }
  .brand-tab{
    position:absolute;right:7px;top:50px;width:352px;height:88px;
    background:var(--green);border-radius:22px 0 0 22px;
    display:flex;align-items:center;gap:12px;padding-left:30px;
  }
  .brand-dot{width:36px;height:36px;border-radius:50%;background:var(--white);flex:none;}
  .brand-name{color:var(--white);font-weight:400;font-size:15px;line-height:1.25;}
  .headline{
    position:absolute;right:40px;top:186px;text-align:right;
    font-weight:700;font-size:49px;line-height:1.08;color:var(--green-head);
    text-shadow:0 0 2px #fff,0 0 6px #fff,2px 2px 0 #fff,-2px -2px 0 #fff,2px -2px 0 #fff,-2px 2px 0 #fff;
  }
  .cta{
    position:absolute;right:40px;top:384px;text-align:right;
    font-size:21px;line-height:1.3;font-weight:400;color:var(--ink);
  }
  .programs-title{
    position:absolute;left:58px;top:516px;
    font-weight:800;font-size:38px;line-height:1.12;color:var(--green-head);letter-spacing:.3px;
  }
  .title-bars{position:absolute;left:600px;top:528px;width:274px;}
  .title-bars span{display:block;background:var(--green);margin-bottom:8px;}
  .title-bars span:nth-child(1){height:9px;}
  .title-bars span:nth-child(2){height:9px;}
  .title-bars span:nth-child(3){height:28px;}
  .program-list{position:absolute;list-style:none;font-weight:600;font-size:18px;}
  .program-list li{position:relative;padding-left:28px;line-height:1.25;margin-bottom:9.5px;}
  .program-list li::before{
    content:"";position:absolute;left:0;top:4px;
    border-left:13px solid var(--green);border-top:8px solid transparent;border-bottom:8px solid transparent;
  }
  .list-left{left:60px;top:612px;}
  .list-right{left:466px;top:612px;width:380px;}
  .badge-circle{
    position:absolute;left:650px;top:800px;width:196px;height:196px;border-radius:50%;
    background:var(--green);border:6px solid #f2f2f8;
  }
  .badge-card{
    position:absolute;left:590px;top:858px;width:290px;height:78px;background:var(--white);
    display:flex;align-items:center;gap:10px;padding-left:22px;
    box-shadow:0 2px 6px rgba(0,0,0,.12);
  }
  .badge-card .brand-dot{width:26px;height:26px;background:var(--green);}
  .badge-card .brand-name{color:var(--green);font-size:13px;}
  .footer{
    position:absolute;left:14px;top:998px;width:899px;height:190px;background:var(--green);
    color:var(--white);border-top:4px solid #eaeaf3;
  }
  .footer-title{text-align:center;font-weight:700;font-size:17px;margin-top:20px;}
  .office{position:absolute;font-size:13.5px;line-height:1.3;}
  .office-left{left:80px;top:52px;width:340px;}
  .office-right{left:486px;top:52px;width:360px;}
  .row{display:flex;gap:12px;margin-bottom:9px;}
  .row svg{flex:none;margin-top:3px;}
  .row strong{font-weight:600;display:block;}
  .website{position:absolute;left:0;right:0;bottom:6px;text-align:center;font-size:14px;font-weight:500;}
</style>
</head>
<body>
<div class="flyer">
  <div class="hero-photo" role="img" aria-label="Photo of a physical therapist guiding a patient through a shoulder stretch in a bright clinic"></div>

  <div class="brand-tab">
    <span class="brand-dot"></span>
    <span class="brand-name">Meadowlark Physical Therapy,<br>Chiropractic, and Acupuncture</span>
  </div>

  <h1 class="headline">WE CREATE<br>HEALTHY<br>FAMILIES.</h1>
  <p class="cta">Call or Make an<br>appointment online today.</p>

  <h2 class="programs-title">2 OFFICE LOCATIONS<br>SPECIALTY PROGRAMS</h2>
  <div class="title-bars"><span></span><span></span><span></span></div>

  <ul class="program-list list-left">
    <li>Work Injury</li>
    <li>Motor Vehicle Accidents</li>
    <li>Spanish Speaking</li>
    <li>Neck and Back Pain</li>
    <li>Shoulder Pain</li>
    <li>Rotator Cuff Disorder</li>
    <li>Bursitis</li>
    <li>Hip Pain</li>
  </ul>
  <ul class="program-list list-right">
    <li>Knee, Ankle, and Foot Pain</li>
    <li>Neck and Back Pain</li>
    <li>Post Operative Care Including<br>Spine, Shoulder, Knee,<br>Total Joint Replacement</li>
  </ul>

  <div class="badge-circle"></div>
  <div class="badge-card">
    <span class="brand-dot"></span>
    <span class="brand-name">Meadowlark Physical Therapy,<br>Chiropractic, and Acupuncture</span>
  </div>

  <footer class="footer">
    <p class="footer-title">MEADOWLARK PHYSICAL THERAPY &amp; CHIROPRACTIC</p>
    <div class="office office-left">
      <div class="row">
        <svg width="16" height="16" viewBox="0 0 16 16"><circle cx="8" cy="8" r="7.5" fill="#fff"/><path d="M8 3.5a3 3 0 0 0-3 3c0 2.2 3 5.5 3 5.5s3-3.3 3-5.5a3 3 0 0 0-3-3z" fill="#6bb446"/><circle cx="8" cy="6.5" r="1.1" fill="#fff"/></svg>
        <div><strong>Dalton Heights Office</strong>48-71 Pinecrest Blvd Dalton Heights,<br>NY 10592</div>
      </div>
      <div class="row">
        <svg width="16" height="16" viewBox="0 0 16 16"><circle cx="8" cy="8" r="7.5" fill="#fff"/><path d="M5.2 4.2l1.6-.3.9 2-1 .8a5 5 0 0 0 2.6 2.6l.8-1 2 .9-.3 1.6c-3.8.2-6.8-2.8-6.6-6.6z" fill="#6bb446"/></svg>
        <div>Phone: 718-582-0147<br>Fax: 718-582-0163</div>
      </div>
    </div>
    <div class="office office-right">
      <div class="row">
        <svg width="16" height="16" viewBox="0 0 16 16"><circle cx="8" cy="8" r="7.5" fill="#fff"/><path d="M8 3.5a3 3 0 0 0-3 3c0 2.2 3 5.5 3 5.5s3-3.3 3-5.5a3 3 0 0 0-3-3z" fill="#6bb446"/><circle cx="8" cy="6.5" r="1.1" fill="#fff"/></svg>
        <div><strong>Fernvale Office</strong>3715 Tillman Parkway, Ste. 315 Fernvale,<br>NY 10592</div>
      </div>
      <div class="row">
        <svg width="16" height="16" viewBox="0 0 16 16"><circle cx="8" cy="8" r="7.5" fill="#fff"/><path d="M5.2 4.2l1.6-.3.9 2-1 .8a5 5 0 0 0 2.6 2.6l.8-1 2 .9-.3 1.6c-3.8.2-6.8-2.8-6.6-6.6z" fill="#6bb446"/></svg>
        <div>Phone: 718-904-3218<br>Fax: 718-904-3229</div>
      </div>
    </div>
    <p class="website">www.meadowlarkptrehab.com</p>
  </footer>
</div>
</body>
</html>
```